Brindle Sky Port needs a new upscale business card design for our high end aircraft hangar complex

Brindle Sky Port (BSP) is a large, upscale jet hangar complex in the US housing expensive aircraft. We need a new business card design, using our current logo. We will be attending a industry convention and need a card design that will stand out and be remembered by aircraft owners and private pilots.

Target Market(s)

Aircraft pilots or owners looking for a new upscale hangar

Industry/Entity Type

Airport

Contact Information for Business Card

I like to use very heavy card stock, 400#, double sided. Square, no rounded edges please.

Colors
3276b5
0255a3
85abd2

Requirements
Must have
• An expensive, classy design, vivid colors.
Nice to have
• Needs to look very expensive and classy, and have some "pop". Designer must be able to download or copy my current typeface or fonts.
• One card side might be black with the "Logo and Brindle Sky Port Double line image in blue (or try gold, or glossy black), and perhaps have a grayed out "K720 jet silhouette". The other card side would have our contact info, and perhaps the "BSP Logo only". I'd like my contact info 'stacked', not in a paragraph format.
Should not have
• Should not look "too busy". Having a double-sided card will help.

```html
<!DOCTYPE html>
<html lang="en">
<head>
<meta charset="utf-8">
<title>Brindle Sky Port – Business Card</title>
<link rel="stylesheet" href="https://fonts.googleapis.com/css2?family=Michroma&family=Open+Sans:ital,wght@0,400;1,600&display=swap">
<style>
  :root {
    --page: #e9e9e9;
    --card-black: #0c0c0d;
    --card-charcoal: #2a2a2c;
    --silver: #d4d4d6;
    --band-light: #ffffff;
    --band-shade: #b9b9bc;
    --ink-dark: #1e1e20;
    --brand-blue: #0255a3;
    --accent-blue: #3276b5;
    --text-light: #f2f2f2;
  }
  * { margin: 0; padding: 0; box-sizing: border-box; }
  html, body { width: 1200px; height: 1020px; overflow: hidden; }
  body {
    background: var(--page);
    font-family: "Open Sans", Arial, sans-serif;
  }
  .card-sheet {
    position: relative;
    width: 1200px;
    height: 1020px;
  }
  .card {
    position: absolute;
    left: 180px;
    width: 840px;
    height: 470px;
    overflow: hidden;
    background: var(--card-black);
  }
  .card--front { top: 30px; }
  .card--back { top: 520px; }

  .card-facets {
    position: absolute;
    inset: 0;
    width: 100%;
    height: 100%;
  }

  /* front */
  .brand-lockup {
    position: absolute;
    left: 0;
    right: 0;
    top: 150px;
    text-align: center;
    font-family: "Michroma", "Arial Black", sans-serif;
    color: var(--silver);
  }
  .brand-lockup__initials {
    display: block;
    font-size: 118px;
    line-height: 1;
    letter-spacing: 10px;
  }
  .brand-lockup__name {
    display: block;
    margin-top: 22px;
    font-size: 34px;
    letter-spacing: 4px;
    text-transform: uppercase;
  }

  /* back */
  .brand-lockup--small {
    top: 128px;
    left: 70px;
    right: auto;
    width: 200px;
  }
  .brand-lockup--small .brand-lockup__initials {
    font-size: 56px;
    letter-spacing: 5px;
  }
  .brand-lockup--small .brand-lockup__name {
    margin-top: 10px;
    font-size: 12px;
    letter-spacing: 1.5px;
  }

  .person {
    position: absolute;
    left: 400px;
    top: 204px;
    width: 400px;
    text-align: center;
  }
  .person__name {
    font-family: "Michroma", "Arial Black", sans-serif;
    font-size: 25px;
    letter-spacing: 1px;
    color: var(--ink-dark);
    white-space: nowrap;
  }
  .person__surname { color: var(--brand-blue); }
  .person__title {
    margin-top: 4px;
    font-size: 18px;
    color: var(--ink-dark);
  }

  .contact-list {
    position: absolute;
    left: 300px;
    top: 326px;
    list-style: none;
    color: var(--text-light);
    font-size: 21px;
    line-height: 32px;
  }
  .contact-list__label { font-style: italic; font-weight: 600; }
  .contact-list__accent { color: var(--accent-blue); }
</style>
</head>
<body>
<main class="card-sheet">

  <section class="card card--front" aria-label="Card front">
    <svg class="card-facets" viewBox="0 0 840 470" preserveAspectRatio="none" aria-hidden="true">
      <defs>
        <linearGradient id="front-top" x1="0" y1="0" x2="0" y2="1">
          <stop offset="0" stop-color="#1c1c1e"/>
          <stop offset="1" stop-color="#050505"/>
        </linearGradient>
        <linearGradient id="front-bottom" x1="0" y1="0" x2="0" y2="1">
          <stop offset="0" stop-color="#222224"/>
          <stop offset="1" stop-color="#0a0a0b"/>
        </linearGradient>
      </defs>
      <rect width="840" height="240" fill="url(#front-top)"/>
      <rect y="240" width="840" height="230" fill="url(#front-bottom)"/>
    </svg>
    <div class="brand-lockup">
      <span class="brand-lockup__initials">BSP</span>
      <span class="brand-lockup__name">Brindle Sky Port</span>
    </div>
  </section>

  <section class="card card--back" aria-label="Card back">
    <svg class="card-facets" viewBox="0 0 840 470" preserveAspectRatio="none" aria-hidden="true">
      <defs>
        <linearGradient id="back-base" x1="0" y1="0" x2="1" y2="1">
          <stop offset="0" stop-color="#242426"/>
          <stop offset="1" stop-color="#0b0b0c"/>
        </linearGradient>
        <linearGradient id="back-panel" x1="0" y1="0" x2="1" y2="0">
          <stop offset="0" stop-color="#151516"/>
          <stop offset="1" stop-color="#323234"/>
        </linearGradient>
        <linearGradient id="silver-band" x1="0" y1="0" x2="0" y2="1">
          <stop offset="0" stop-color="#ffffff"/>
          <stop offset="0.6" stop-color="#eeeeef"/>
          <stop offset="1" stop-color="#b9b9bc"/>
        </linearGradient>
      </defs>
      <rect width="840" height="470" fill="url(#back-base)"/>
      <polygon points="590,0 840,0 840,166 395,166" fill="url(#back-panel)"/>
      <polygon points="590,0 395,166 260,284 120,470 0,470 0,470 260,284" fill="#050505" opacity="0.55"/>
      <polygon points="395,166 840,166 840,284 260,284" fill="url(#silver-band)"/>
      <line x1="395" y1="166" x2="840" y2="166" stroke="#8a8a8d" stroke-width="1"/>
    </svg>

    <div class="brand-lockup brand-lockup--small">
      <span class="brand-lockup__initials">BSP</span>
      <span class="brand-lockup__name">Brindle Sky Port</span>
    </div>

    <div class="person">
      <p class="person__name">DORIAN K. <span class="person__surname">HALE</span></p>
      <p class="person__title">Logistic director</p>
    </div>

    <ul class="contact-list">
      <li><span class="contact-list__label">phone:</span> +555.010.2468</li>
      <li><span class="contact-list__label">e-mail:</span> dorian.hale@<span class="contact-list__accent">brindle</span>skyport.com</li>
      <li><span class="contact-list__label">website:</span> <span class="contact-list__accent">brindle</span>skyport.com</li>
    </ul>
  </section>

</main>
</body>
</html>
```